New Business Card for Web Design/Internet Marketing Company

Looking for a great looking new business card. We are a 10 year old web design, internet marketing and website management company that works mostly with small businesses.

Our new card needs to better match the colors and style of our website, be bold, extremely usable and slightly edgy.

Target Market(s)

Small/Medium businesses that have websites

Industry/Entity Type

Internet

Requirements
Must have
• Front and back design, full color, rounded corners please

Must use the colors/style of our website (JPG provided)

INFO FOR CARDS (as readable as possible please)
Mark Lenner
President/CEO
mark@trelvanmedia.example
Phone: 520-381-7459
Toll Free: 866-381-7459
Address: 4315 W. Calloway Ave. Ste. 140, Tucson, AZ 85792

THINGS I WANT TO PROMOTE (if there is room):
1. Our Website - www.trelvanmedia.example

2. Social Media
Twitter: @trelvanmedia
Facebook: www.facebook.com/trelvanmedia

3. Our Services
Web Design
Internet Marketing
Website Management

```html
<!DOCTYPE html>
<html lang="en">
<head>
<meta charset="utf-8">
<title>Trelvan Media – Business Cards</title>
<link rel="stylesheet" href="https://fonts.googleapis.com/css2?family=Source+Sans+3:wght@400;600;700&display=swap">
<style>
  :root {
    --brand-blue: #1190c9;
    --brand-orange: #f5862b;
    --ink-black: #060606;
    --paper-white: #ffffff;
    --text-grey: #4a4a4a;
    --text-light: #f2f2f2;
    --backdrop: #e7e3dd;
    --card-radius: 15px;
  }
  * { box-sizing: border-box; margin: 0; padding: 0; }
  html, body {
    width: 1200px; height: 761px; overflow: hidden;
    background: var(--backdrop);
    font-family: "Source Sans 3", "Myriad Pro", Arial, sans-serif;
  }
  .canvas { position: relative; width: 1200px; height: 761px; }

  .card {
    position: absolute; width: 525px; height: 300px;
    border-radius: var(--card-radius); overflow: hidden;
    box-shadow: 0 2px 6px rgba(0,0,0,.25);
  }
  .card--front-dark { left: 47px; top: 65px; background: var(--ink-black); color: var(--text-light); }
  .card--front-light { left: 612px; top: 65px; background: var(--paper-white); color: var(--text-grey); }
  .card--back { left: 370px; top: 403px; background: var(--paper-white); color: var(--text-grey); border: 1px solid #9a9a9a; }

  .card__header { position: absolute; inset: 0; width: 525px; height: 300px; }

  .card__person { position: absolute; right: 36px; top: 10px; text-align: right; color: var(--paper-white); }
  .card__name { font-size: 21px; font-weight: 700; line-height: 1.2; }
  .card__title { font-size: 15px; font-weight: 400; line-height: 1.2; }

  .brand-name {
    position: absolute; font-weight: 700; color: var(--brand-orange);
    letter-spacing: -0.5px; white-space: nowrap; line-height: 1;
  }
  .card--front-dark .brand-name,
  .card--front-light .brand-name { left: 32px; top: 108px; font-size: 46px; }
  .card--back .brand-name { left: 0; right: 0; top: 72px; text-align: center; font-size: 48px; }

  .contact-list { position: absolute; left: 31px; top: 196px; list-style: none; font-size: 13.5px; }
  .contact-list li { display: flex; align-items: center; height: 18.5px; }
  .contact-list svg { width: 11px; height: 11px; margin-right: 8px; flex: none; }
  .card--front-dark .contact-list svg { fill: var(--text-light); stroke: var(--text-light); }
  .card--front-light .contact-list svg { fill: var(--text-grey); stroke: var(--text-grey); }

  .divider { position: absolute; left: 238px; top: 230px; width: 1px; height: 42px; }
  .card--front-dark .divider { background: #bdbdbd; }
  .card--front-light .divider { background: #9a9a9a; }

  .address { position: absolute; left: 260px; top: 235px; font-size: 13.5px; line-height: 18px; font-style: normal; }

  .services { position: absolute; left: 0; right: 0; top: 180px; text-align: center; font-size: 17.5px; font-weight: 700; color: var(--brand-blue); line-height: 23px; }
  .services span::before {
    content: ""; display: inline-block; width: 8px; height: 8px; border-radius: 50%;
    background: var(--brand-orange); margin: 0 6px 2px 10px; vertical-align: middle;
  }
  .social { position: absolute; left: 0; right: 0; top: 251px; display: flex; justify-content: center; gap: 14px; font-size: 17px; }
  .social__item { display: flex; align-items: center; }
  .social__mark { width: 14px; height: 14px; background: var(--brand-blue); border-radius: 2px; margin-right: 6px; }
</style>
</head>
<body>
<main class="canvas">

  <!-- Front, dark edition -->
  <section class="card card--front-dark" aria-label="Business card front, black">
    <svg class="card__header" viewBox="0 0 525 300" aria-hidden="true">
      <path d="M0 0 H525 V114 C420 60 250 28 0 40 Z" fill="var(--brand-blue)"/>
      <path d="M0 40 C250 28 420 60 525 114 V142 C430 88 250 46 0 62 Z" fill="var(--ink-black)"/>
      <path d="M0 46 C250 34 420 66 525 120 V142 C430 94 250 52 0 62 Z" fill="var(--brand-orange)"/>
    </svg>
    <div class="card__person">
      <p class="card__name">Mark Lenner</p>
      <p class="card__title">President/CEO</p>
    </div>
    <p class="brand-name">Trelvan Media</p>
    <ul class="contact-list">
      <li><svg viewBox="0 0 12 12"><path d="M3 1 L5 4 L4 5 Q5 7 7 8 L8 7 L11 9 L10 11 Q4 11 1 3 Z" stroke="none"/></svg>866-381-7459</li>
      <li><svg viewBox="0 0 12 12"><path d="M3 1 L5 4 L4 5 Q5 7 7 8 L8 7 L11 9 L10 11 Q4 11 1 3 Z" stroke="none"/></svg>520-381-7459</li>
      <li><svg viewBox="0 0 12 12"><rect x="1" y="3" width="10" height="7" stroke="none"/><path d="M1 3 L6 7 L11 3" fill="none" stroke="#060606" stroke-width="1"/></svg>mark@trelvanmedia.example</li>
      <li><svg viewBox="0 0 12 12"><circle cx="6" cy="6" r="5" stroke="none"/><path d="M1 6 H11 M6 1 V11" fill="none" stroke="#060606" stroke-width=".8"/></svg>www.trelvanmedia.example</li>
    </ul>
    <div class="divider"></div>
    <address class="address">4315 W. Calloway Ave. Ste. 140<br>Tucson, AZ 85792</address>
  </section>

  <!-- Front, light edition -->
  <section class="card card--front-light" aria-label="Business card front, white">
    <svg class="card__header" viewBox="0 0 525 300" aria-hidden="true">
      <path d="M0 0 H525 V114 C420 60 250 28 0 40 Z" fill="var(--brand-blue)"/>
      <path d="M0 46 C250 34 420 66 525 120 V142 C430 94 250 52 0 62 Z" fill="var(--brand-orange)"/>
    </svg>
    <div class="card__person">
      <p class="card__name">Mark Lenner</p>
      <p class="card__title">President/CEO</p>
    </div>
    <p class="brand-name">Trelvan Media</p>
    <ul class="contact-list">
      <li><svg viewBox="0 0 12 12"><path d="M3 1 L5 4 L4 5 Q5 7 7 8 L8 7 L11 9 L10 11 Q4 11 1 3 Z" stroke="none"/></svg>866-381-7459</li>
      <li><svg viewBox="0 0 12 12"><path d="M3 1 L5 4 L4 5 Q5 7 7 8 L8 7 L11 9 L10 11 Q4 11 1 3 Z" stroke="none"/></svg>520-381-7459</li>
      <li><svg viewBox="0 0 12 12"><rect x="1" y="3" width="10" height="7" stroke="none"/><path d="M1 3 L6 7 L11 3" fill="none" stroke="#ffffff" stroke-width="1"/></svg>mark@trelvanmedia.example</li>
      <li><svg viewBox="0 0 12 12"><circle cx="6" cy="6" r="5" stroke="none"/><path d="M1 6 H11 M6 1 V11" fill="none" stroke="#ffffff" stroke-width=".8"/></svg>www.trelvanmedia.example</li>
    </ul>
    <div class="divider"></div>
    <address class="address">4315 W. Calloway Ave. Ste. 140<br>Tucson, AZ 85792</address>
  </section>

  <!-- Back -->
  <section class="card card--back" aria-label="Business card back">
    <p class="brand-name">Trelvan Media</p>
    <div class="services">
      <p><span>Web Design</span><span>Internet Marketing</span></p>
      <p><span>Website Management</span></p>
    </div>
    <div class="social">
      <p class="social__item"><span class="social__mark"></span>@trelvanmedia</p>
      <p class="social__item"><span class="social__mark"></span>trelvanmedia</p>
    </div>
  </section>

</main>
</body>
</html>
```